Law Firm Business Card

This is a business card for a law firm that serves US military and veterans.

The card must have ONLY the following (we want an uncluttered look):

- Company logo (PNG, GIF, JPEG copies uploaded)
- A tagline reading: "a law firm for service members and veterans"
- My name and title: "Tobias Marlow" and "Attorney"
- My email: "tobias.marlow@brinmoorlegal.com"
- My number: "855-FIRM-ONE (347-6663)"

We are looking for a clean, simple layout with only the above information, likely printed on a bright white cotton stock. The font of our logo is DIN 1451, and the font used on our website is Helvetica Neue. The color of our logo is #336699, and we probably want the tagline in that color also, and my contact information in a dark grey. Please review our website at www.brinmoorlegal.com to ensure your card design complements our website style.

Thanks and we look forward to seeing your submissions.

A few notes:

- Two-sided submissions are ok
- Please don't add graphics (scales of justice, judges hammer, etc)

```html
<!DOCTYPE html>
<html lang="en">
<head>
<meta charset="utf-8">
<title>Brinmoor Legal – Business Card</title>
<link rel="stylesheet" href="https://fonts.googleapis.com/css2?family=Lato:wght@400;700&display=swap">
<style>
  :root {
    --backdrop: #6e6e6e;
    --card-white: #ffffff;
    --brand-blue: #336699;
    --band-blue: #2f6aa3;
    --navy: #163a63;
    --label-blue: #6f9fd1;
    --title-blue: #8fb2d8;
    --text-white: #ffffff;
  }

  * { box-sizing: border-box; margin: 0; padding: 0; }

  html, body {
    width: 1200px;
    height: 900px;
    overflow: hidden;
    background: var(--backdrop);
    font-family: "Lato", "Helvetica Neue", Arial, sans-serif;
  }

  .canvas {
    width: 1200px;
    height: 900px;
    display: flex;
    align-items: center;
    justify-content: center;
  }

  .business-card {
    position: relative;
    width: 1050px;
    height: 600px;
    border-radius: 28px;
    overflow: hidden;
    background: var(--card-white);
    display: flex;
    flex-direction: column;
  }

  .card-header {
    height: 282px;
    display: flex;
    align-items: center;
    justify-content: center;
  }

  .firm-name {
    color: var(--brand-blue);
    font-size: 64px;
    font-weight: 700;
    line-height: 1;
  }

  .tagline-band {
    height: 56px;
    background: var(--band-blue);
    display: flex;
    align-items: center;
    justify-content: center;
  }

  .tagline {
    color: var(--text-white);
    font-size: 27px;
    font-weight: 700;
    letter-spacing: 2.5px;
    text-transform: uppercase;
    white-space: nowrap;
  }

  .card-body {
    flex: 1;
    background: var(--navy);
    position: relative;
  }

  .attorney {
    position: absolute;
    top: 62px;
    left: 0;
    right: 0;
    text-align: center;
    color: var(--text-white);
    font-size: 48px;
    font-weight: 400;
    letter-spacing: 0.5px;
    white-space: nowrap;
  }

  .attorney__last {
    font-weight: 700;
    margin-left: 20px;
  }

  .attorney__title {
    margin-left: 14px;
    font-size: 27px;
    font-weight: 400;
    color: var(--title-blue);
    letter-spacing: 1px;
    text-transform: uppercase;
  }

  .contact-row {
    position: absolute;
    left: 64px;
    right: 56px;
    bottom: 58px;
    display: flex;
    justify-content: space-between;
    align-items: baseline;
    color: var(--text-white);
    font-size: 24px;
    white-space: nowrap;
  }

  .contact--phone { transform: translateY(-18px); }

  .contact__label {
    color: var(--label-blue);
    font-weight: 700;
  }

  .contact__value { font-weight: 700; }
</style>
</head>
<body>
  <main class="canvas">
    <article class="business-card">
      <header class="card-header">
        <p class="firm-name">Brinmoor Legal</p>
      </header>

      <div class="tagline-band">
        <p class="tagline">A law firm for service members and veterans</p>
      </div>

      <section class="card-body">
        <h1 class="attorney">
          <span class="attorney__first">Tobias</span><span class="attorney__last">Marlow</span><span class="attorney__title">Attorney</span>
        </h1>

        <div class="contact-row">
          <p class="contact contact--email">
            <span class="contact__label">email :</span>
            <span class="contact__value">tobias.marlow@brinmoorlegal.com</span>
          </p>
          <p class="contact contact--phone">
            <span class="contact__label">number :</span>
            <span class="contact__value">855-FIRM-ONE (347-6663)</span>
          </p>
        </div>
      </section>
    </article>
  </main>
</body>
</html>
```